Business card for Eyelash extension salon in Beverly Hills,California USA

We need new business card for our salon in Beverly Hills. The salon name is 'Lashvera' . We would like to have...Business name: Lashvera Name of person: will provide later Address 4720 N.Alder Crest Ave Beverly Hills , CA 90210 Phone: will provide later (Text only) Web: www.lashverastudio.example plain shape icon, plain shape icon follow us for seasonal campaign and news @lashverastudiolounge Design should look elegant, high-end, clean, simple, cohesive with my brand. Please refer my brand board. Business name color will be metallic bronzy color. Im thinking grey background or white background. Thanks

Target Market(s)

25-35. Gender neutral. People who are in Entertainment business industry.
This is High-end Eyelash extension salon in Beverly Hills

Industry/Entity Type

Beauty Salon

Contact Information for Business Card

Business name: Lashvera
Name of person: will provide later
Address 4720 N.Alder Crest Ave Beverly Hills , CA 90210
Phone: will provide later (Text only)
Web: www.lashverastudio.example
plain shape icon, plain shape icon
follow us for seasonal campaign and news @lashverastudiolounge

Requirements
Must have
• Beautiful, elegant, clean and simple look but very attractive and modern
Should not have
• We don't like too clutter, too busy designs.

```html
<!DOCTYPE html>
<html lang="en">
<head>
<meta charset="utf-8">
<title>Lashvera Beverly Hills – Business Card</title>
<link rel="stylesheet" href="https://fonts.googleapis.com/css2?family=Cormorant+Garamond:wght@400;700&family=Josefin+Sans:wght@300;400&display=swap">
<style>
  :root {
    --backdrop: #dcdcdc;
    --card: #ffffff;
    --card-field: #f8f8f8;
    --bronze: #8a6a50;
    --ink-grey: #7d7d7d;
    --rule-grey: #9a9a9a;
    --icon-grey: #a8a8a8;
    --eye-grey: #c9c9c9;
  }
  * { margin: 0; padding: 0; box-sizing: border-box; }
  html, body { width: 1200px; height: 960px; overflow: hidden; }
  body { background: var(--backdrop); position: relative; font-family: "Josefin Sans", sans-serif; }

  .card {
    position: absolute;
    width: 600px;
    height: 343px;
    background: var(--card);
  }
  .card--front { left: 302px; top: 122px; }
  .card--back { left: 299px; top: 495px; }

  .card__frame {
    position: absolute;
    inset: 15px 15px 15px 15px;
    border: 2px solid var(--bronze);
    background: var(--card-field);
  }
  .card--front .card__frame { inset: 16px 15px 15px 15px; }

  .eyes-art {
    position: absolute;
    left: 258px;
    top: 84px;
    width: 84px;
    height: 18px;
    background: linear-gradient(90deg, transparent, var(--eye-grey) 20%, var(--eye-grey) 80%, transparent);
    opacity: .45;
    border-radius: 9px;
  }

  .holder-name {
    position: absolute;
    left: 0; right: 0;
    top: 123px;
    text-align: center;
    font-family: "Cormorant Garamond", serif;
    font-weight: 700;
    font-size: 25px;
    letter-spacing: 1px;
    color: var(--bronze);
    line-height: 1;
  }

  .role-row {
    position: absolute;
    left: 151px;
    width: 291px;
    top: 152px;
    display: flex;
    align-items: center;
    gap: 4px;
  }
  .rule { flex: 1; height: 1px; background: var(--rule-grey); }
  .role {
    font-family: "Cormorant Garamond", serif;
    font-weight: 700;
    font-size: 13px;
    letter-spacing: 1.5px;
    color: var(--icon-grey);
    line-height: 1;
  }

  .contact {
    position: absolute;
    left: 0; right: 0;
    top: 183px;
    text-align: center;
    font-weight: 300;
    font-size: 13.5px;
    line-height: 18px;
    color: var(--ink-grey);
  }

  .social-row {
    position: absolute;
    left: 151px;
    width: 291px;
    top: 240px;
    display: flex;
    align-items: center;
    gap: 3px;
  }
  .social-row svg { display: block; }

  .wordmark {
    position: absolute;
    left: 0; right: 0;
    top: 62px;
    text-align: center;
    font-family: "Cormorant Garamond", serif;
    font-weight: 400;
    font-size: 128px;
    line-height: 1;
    color: var(--bronze);
  }
  .locale {
    position: absolute;
    left: 289px;
    top: 251px;
    font-weight: 400;
    font-size: 13px;
    letter-spacing: 3px;
    color: var(--bronze);
  }
</style>
</head>
<body>

  <section class="card card--front">
    <div class="card__frame"></div>
    <div class="eyes-art" role="img" aria-label="Small line illustration of closed eyes with lashes"></div>
    <h1 class="holder-name">KAEDE</h1>
    <div class="role-row">
      <span class="rule"></span>
      <span class="role">OWNER</span>
      <span class="rule"></span>
    </div>
    <p class="contact">
      4720 N.Alder Crest Ave, Beverly Hills, CA 90210<br>
      310.555.0148 | hello@lashverastudio.example | lashverastudio.example
    </p>
    <div class="social-row">
      <span class="rule"></span>
      <svg width="60" height="20" viewBox="0 0 60 20" role="img" aria-label="Social media links">
        <polygon points="10,0 18.7,5 18.7,15 10,20 1.3,15 1.3,5" fill="var(--icon-grey)"/>
        <polygon points="30,0 38.7,5 38.7,15 30,20 21.3,15 21.3,5" fill="var(--icon-grey)"/>
        <polygon points="50,0 58.7,5 58.7,15 50,20 41.3,15 41.3,5" fill="var(--icon-grey)"/>
      </svg>
      <span class="rule"></span>
    </div>
  </section>

  <section class="card card--back">
    <div class="card__frame"></div>
    <h2 class="wordmark">Lashvera</h2>
    <p class="locale">BEVERLY HILLS</p>
  </section>

</body>
</html>
```